White Paper and One-Page Advertisement for TELVORISH-QM

I need both documents to be better formatted and designed so they look professional, not something someone with mediocre word skills put together. They will go out to 1000s of industry professionals, and they need to look sharp. I need them to have my company's color palate logo, and branding on it similar to how it is now, but better. Please do not change any of the written content, but it can be arranged in any other format you think is better. Smart art and things i've already used can be omitted in favor of better designs. The developer is free to use their creativity. White paper should not be longer than the three pages unless necessary.

Target Market(s)

Life Sciences supply chain professionals

Colors
33b8a4
0592cd
9bcb3c
fbee3e
3277b5

Requirements
Must have
• Must be professional looking and not look like something done in word. Please use the color palate as seen on the documents.
Should not have
• Any changes to the written content.

```html
<!DOCTYPE html>
<html lang="en">
<head>
<meta charset="utf-8">
<title>TELVORISH-QM One-Page Advertisement</title>
<link href="https://fonts.googleapis.com/css2?family=Montserrat:wght@400;500;600;700&display=swap" rel="stylesheet">
<style>
  :root {
    --teal: #1f7f6e;
    --teal-bright: #33b8a4;
    --blue: #2a6fb8;
    --lime: #9bcb3c;
    --lime-soft: #b7e05a;
    --yellow: #fbee3e;
    --ink: #333a3f;
    --white: #ffffff;
    --page-bg: #ffffff;
  }
  * { box-sizing: border-box; margin: 0; padding: 0; }
  html, body { width: 1200px; height: 1200px; overflow: hidden; background: var(--page-bg); }
  body { font-family: "Montserrat", sans-serif; color: var(--ink); position: relative; }

  .flyer {
    position: absolute; left: 140px; top: 6px;
    width: 920px; height: 1188px; background: var(--white); overflow: hidden;
  }
  .hero {
    position: absolute; left: 0; top: 0; width: 920px; height: 620px;
    background: linear-gradient(160deg, #5a3a2a 0%, #7c5440 30%, #c9a46a 55%, #3d6b6e 80%, #2f5556 100%);
  }
  .brand {
    position: absolute; left: 0; top: 70px; width: 920px; text-align: center; color: var(--white);
  }
  .brand-dot {
    width: 64px; height: 64px; border: 3px solid var(--white); border-radius: 50%; margin: 0 auto 14px;
  }
  .brand-name { font-weight: 700; font-size: 30px; letter-spacing: 1px; }

  .section-tag {
    position: absolute; display: flex; align-items: flex-end;
  }
  .section-tag .label {
    background: var(--teal); color: var(--white); font-weight: 600; padding: 0 26px 0 10px;
    clip-path: polygon(0 0, 100% 0, calc(100% - 8px) 100%, 0 100%);
    display: flex; align-items: center;
  }
  .section-tag .slash {
    width: 10px; background: var(--lime); margin-left: -4px;
    clip-path: polygon(0 0, 45% 0, 100% 100%, 55% 100%);
  }
  .section-tag .rule { height: 2px; background: var(--lime); flex: 1; }

  .tag-platform { left: 43px; top: 642px; width: 471px; height: 33px; }
  .tag-platform .label { color: var(--yellow); font-size: 22px; height: 33px; }
  .tag-platform .slash { height: 33px; }
  .tag-benefits { left: 43px; top: 913px; width: 836px; height: 24px; }
  .tag-benefits .label { font-size: 17px; height: 24px; padding-right: 20px; }
  .tag-benefits .slash { height: 24px; }
  .tag-promise { left: 43px; top: 1062px; width: 836px; height: 24px; }
  .tag-promise .label { font-size: 17px; height: 24px; padding-right: 24px; }
  .tag-promise .slash { height: 24px; }

  .check-list { list-style: none; font-size: 14.6px; line-height: 18.5px; }
  .check-list li { position: relative; padding-left: 26px; }
  .check-list li::before {
    content: ""; position: absolute; left: 2px; top: 4px; width: 11px; height: 11px;
    border-radius: 50%; background: var(--teal);
  }
  .check-list li::after {
    content: ""; position: absolute; left: 5.5px; top: 6px; width: 3px; height: 5px;
    border: solid var(--white); border-width: 0 1.5px 1.5px 0; transform: rotate(45deg);
  }
  .platform-list { position: absolute; left: 43px; top: 692px; width: 490px; }
  .platform-list li { margin-bottom: 8.5px; }

  .benefit-list { position: absolute; top: 950px; }
  .benefit-list li { margin-bottom: 8.5px; }
  .benefits-left { left: 43px; width: 390px; }
  .benefits-left li { padding-left: 16px; }
  .benefits-left li::before { left: 0; }
  .benefits-left li::after { left: 3.5px; }
  .benefits-right { left: 441px; width: 450px; }

  .process-flow { position: absolute; left: 562px; top: 653px; width: 316px; height: 273px; }
  .process-flow text { font-family: "Montserrat", sans-serif; font-size: 13.4px; font-weight: 600; fill: var(--white); }

  .promise-text { position: absolute; left: 45px; top: 1096px; font-size: 14.6px; }

  .contact-band { position: absolute; left: 0; top: 1131px; width: 920px; height: 57px; }
  .contact-item {
    position: absolute; top: 1145px; display: flex; align-items: center; gap: 14px;
    font-size: 17.5px; font-weight: 500;
  }
  .contact-phone { left: 46px; color: var(--white); }
  .contact-email { left: 322px; color: var(--ink); }
  .contact-web { left: 606px; color: var(--ink); }
</style>
</head>
<body>
<main class="flyer">
  <section class="hero" role="img" aria-label="Photograph of people in traditional ceremonial dress sharing a joyful moment under a carved wooden roof"></section>
  <div class="brand">
    <div class="brand-dot"></div>
    <div class="brand-name">TELVORISH-QM</div>
  </div>

  <div class="section-tag tag-platform"><span class="label">Our Platform</span><span class="slash"></span><span class="rule"></span></div>
  <ul class="check-list platform-list">
    <li>A multi-vendor marketplace for the life science community to transact pre-market and after-market materials and equipment</li>
    <li>Researchers, manufactures, &amp; original suppliers can create an account to buy, sell, or donate materials</li>
    <li>Part 11 compliant signature and authentication</li>
    <li>Leverages industry auditing skills to facilitate compliant and transparent transactions</li>
    <li>Some of the best and industry vendors and software used</li>
  </ul>

  <svg class="process-flow" viewBox="0 0 295 255" aria-label="Process steps">
    <polygon fill="#2a6fb8" points="0,11 178,11 178,0 222,46 178,92 178,80 0,80"/>
    <text x="18" y="42">Authentication &amp;</text>
    <text x="18" y="58">terms of quality</text>
    <polygon fill="#1f7f6e" points="27,80 205,80 205,62 250,107 205,150 205,135 27,135"/>
    <text x="45" y="112">Set up store</text>
    <polygon fill="#2a6fb8" points="44,137 222,137 222,122 267,165 222,210 222,190 44,190"/>
    <text x="54" y="158">Seamlessly trasnact</text>
    <text x="54" y="174">&amp; request for information</text>
    <polygon fill="#1f7f6e" points="71,192 250,192 250,172 295,215 250,255 250,243 71,243"/>
    <text x="91" y="223">Check out and sign</text>
  </svg>

  <div class="section-tag tag-benefits"><span class="label">Benefits</span><span class="slash"></span><span class="rule"></span></div>
  <ul class="check-list benefit-list benefits-left">
    <li>Reduce write-offs by selling excess and obsolete materials, equipment, spare parts, etc.</li>
    <li>Buy quality materials at a reduced price.</li>
    <li>Market materials if an original supplier</li>
  </ul>
  <ul class="check-list benefit-list benefits-right">
    <li>Donate material to researchers</li>
    <li>Acquire donated materials</li>
    <li>Collaborate and consort to reduce supply chain risk such as mutual aid agreements, joint supplier audits, etc.</li>
  </ul>

  <div class="section-tag tag-promise"><span class="label">Our Promise</span><span class="slash"></span><span class="rule"></span></div>
  <p class="promise-text">A greener, more cost-efficient, and quality driven supply chain through a collaborative life sciences marketplace.</p>

  <svg class="contact-band" viewBox="0 0 920 57" preserveAspectRatio="none">
    <rect width="920" height="57" fill="#1f7f6e"/>
    <polygon points="246,0 920,0 920,40 268,40" fill="#ffffff"/>
    <polygon points="252,0 920,0 920,36 272,36" fill="#b7e05a"/>
  </svg>
  <div class="contact-item contact-phone">
    <svg width="22" height="22" viewBox="0 0 24 24"><path d="M6.6 10.8a15 15 0 0 0 6.6 6.6l2.2-2.2a1 1 0 0 1 1-.25 11.4 11.4 0 0 0 3.6.57 1 1 0 0 1 1 1V20a1 1 0 0 1-1 1A17 17 0 0 1 3 4a1 1 0 0 1 1-1h3.5a1 1 0 0 1 1 1c0 1.25.2 2.45.57 3.6a1 1 0 0 1-.25 1z" fill="none" stroke="#ffffff" stroke-width="1.6"/></svg>
    <span>844-555-TVQM</span>
  </div>
  <div class="contact-item contact-email">
    <svg width="22" height="16" viewBox="0 0 22 16"><rect x="1" y="1" width="20" height="14" fill="#1f7f6e"/><path d="M1 1l10 8 10-8" fill="none" stroke="#b7e05a" stroke-width="1.5"/></svg>
    <span>info@telvorishqm.com</span>
  </div>
  <div class="contact-item contact-web">
    <svg width="20" height="20" viewBox="0 0 20 20" fill="none" stroke="#1f7f6e" stroke-width="1.4"><circle cx="10" cy="10" r="8.5"/><ellipse cx="10" cy="10" rx="3.8" ry="8.5"/><path d="M1.5 10h17M3 5.5h14M3 14.5h14"/></svg>
    <span>www.telvorishqm.com</span>
  </div>
</main>
</body>
</html>
```